electronics flyer required for small business

We need a flyer designed to advertise the services that our company Vorla-Electronics can provide. These services include installation or repair of phone systems, door intercoms / access controls, CCTV, Security systems, mobile phone signal boosting, digital TV services, network systems and sockets , basically anything electronics we can look at doing. We would like them to call us if they have any electronics based enquires. Free no obligation quote provided

Target Market(s)

small business

Industry/Entity Type

Small Business

Requirements
Must have
• contact details
• 01638405912
• 07481326970
• enquiries@vorla-systems.net
Nice to have
• memorable and eye catching

```html
<!DOCTYPE html>
<html lang="en">
<head>
<meta charset="utf-8">
<title>Vorla-Electronics Flyer</title>
<link rel="stylesheet" href="https://fonts.googleapis.com/css2?family=Open+Sans:wght@400;600;700;800&display=swap">
<style>
  :root {
    --brand-blue: #1b74c2;
    --ring-blue: #74c7f0;
    --ink: #1d1d1d;
    --paper: #ffffff;
    --backdrop: #eeeeee;
    --note-dark: #23858f;
    --note-light: #62b9bc;
  }
  html, body {
    margin: 0;
    width: 885px;
    height: 1200px;
    overflow: hidden;
    background: var(--backdrop);
    font-family: "Open Sans", sans-serif;
  }
  .flyer {
    position: absolute;
    left: 80px;
    top: 88px;
    width: 725px;
    height: 1025px;
    background: var(--paper);
    overflow: hidden;
    box-shadow: 0 2px 10px rgba(0,0,0,.15);
  }
  .header-band {
    position: absolute;
    left: 0; top: 0;
    width: 725px; height: 87px;
    background: var(--brand-blue);
  }
  .brand-name {
    position: absolute;
    left: 0; top: 10px;
    width: 725px;
    text-align: center;
    margin: 0;
    font-size: 52px;
    font-weight: 700;
    color: var(--paper);
    letter-spacing: 1px;
    line-height: 70px;
  }
  .side-strip {
    position: absolute;
    left: 72px; top: 87px;
    width: 133px; height: 860px;
    background: var(--brand-blue);
  }
  .hero-photo {
    position: absolute;
    left: 212px; top: 87px;
    width: 513px; height: 380px;
    background: linear-gradient(160deg, #f7f7f5 0%, #ece6df 45%, #d9c7b4 70%, #eef1f4 100%);
  }
  .service-photo {
    position: absolute;
    left: 35px;
    width: 190px; height: 190px;
    border-radius: 50%;
    border: 10px solid var(--ring-blue);
    box-sizing: content-box;
  }
  .photo-phones { top: 117px; background: radial-gradient(circle at 55% 50%, #3b3b3b 0%, #8a8a8a 45%, #f2f2f2 80%); }
  .photo-intercom { top: 317px; background: radial-gradient(circle at 45% 45%, #9aa3a8 0%, #c9cfd2 50%, #eef0f1 85%); }
  .photo-camera { top: 517px; background: radial-gradient(circle at 40% 40%, #2a2a2a 0%, #8d8d8d 45%, #e4e4e4 85%); }
  .photo-keypad { top: 712px; background: radial-gradient(circle at 50% 55%, #b8b8b8 0%, #dcdcdc 50%, #f3f3f3 85%); }
  .services-heading {
    position: absolute;
    left: 262px; top: 472px;
    display: flex; align-items: center; gap: 12px;
    margin: 0;
    font-size: 27px; font-weight: 600;
    color: var(--brand-blue);
  }
  .services-heading svg { width: 34px; height: 34px; }
  .service-list {
    position: absolute;
    left: 283px; top: 532px;
    margin: 0; padding: 0;
    list-style: none;
    font-size: 19.5px;
    color: var(--ink);
  }
  .service-list li { height: 33px; line-height: 33px; }
  .service-list li::before { content: "» "; }
  .call-to-action {
    position: absolute;
    left: 290px; top: 800px;
    width: 300px; height: 140px;
  }
  .cta-j {
    position: absolute; left: 0; top: -18px;
    font-size: 150px; font-weight: 400; line-height: 150px;
    color: var(--brand-blue);
  }
  .cta-just {
    position: absolute; left: 56px; top: 6px;
    font-size: 58px; line-height: 60px; color: var(--brand-blue);
  }
  .cta-call {
    position: absolute; left: 50px; top: 62px;
    font-size: 58px; line-height: 60px; color: var(--ink);
  }
  .cta-call span { color: var(--brand-blue); }
  .quote-note {
    position: absolute;
    left: 540px; top: 805px;
    width: 138px; height: 112px;
    background: linear-gradient(135deg, var(--note-dark), var(--note-light));
    transform: rotate(-14deg);
    box-shadow: 3px 4px 8px rgba(0,0,0,.35);
    display: flex; align-items: center; justify-content: center;
    text-align: center;
    color: var(--paper);
    font-size: 17px; font-weight: 700; line-height: 22px;
  }
  .footer-band {
    position: absolute;
    left: 0; top: 942px;
    width: 725px; height: 83px;
    background: var(--brand-blue);
    color: var(--paper);
    font-weight: 700;
  }
  .phone-icon { position: absolute; left: 22px; top: 14px; width: 68px; height: 56px; }
  .phone-numbers { position: absolute; left: 105px; top: 12px; font-size: 24px; line-height: 30px; }
  .email { position: absolute; right: 22px; top: 27px; font-size: 19px; }
</style>
</head>
<body>
  <main class="flyer">
    <div class="header-band"></div>
    <h1 class="brand-name">Vorla-Electronics</h1>
    <div class="side-strip"></div>
    <div class="hero-photo" role="img" aria-label="Photo of a smiling family with a laptop on a sofa in a bright living room"></div>

    <div class="service-photo photo-phones" role="img" aria-label="Photo of an office phone system with desk handsets"></div>
    <div class="service-photo photo-intercom" role="img" aria-label="Photo of a video door intercom panel"></div>
    <div class="service-photo photo-camera" role="img" aria-label="Photo of a wall-mounted CCTV camera"></div>
    <div class="service-photo photo-keypad" role="img" aria-label="Photo of a hand using a security alarm keypad"></div>

    <h2 class="services-heading">
      <svg viewBox="0 0 34 34" aria-hidden="true"><circle cx="17" cy="17" r="17" fill="#1b74c2"/><path d="M13 9 L22 17 L13 25" fill="none" stroke="#fff" stroke-width="3" stroke-linecap="round" stroke-linejoin="round"/></svg>
      Services:
    </h2>
    <ul class="service-list">
      <li>Installation Or Repair Of Phone Systems</li>
      <li>Door Intercoms / Access Controls</li>
      <li>CCTV</li>
      <li>Security Systems</li>
      <li>Mobile Phone Signal Boosting</li>
      <li>Digital Tv Services</li>
      <li>Network Systems And Sockets</li>
      <li>Basically Anything Electronics</li>
    </ul>

    <div class="call-to-action">
      <span class="cta-j">J</span>
      <span class="cta-just">ust</span>
      <span class="cta-call">call<span>Us..</span></span>
    </div>
    <div class="quote-note">FREE NO<br>OBLIGATION<br>QUOTE</div>

    <footer class="footer-band">
      <svg class="phone-icon" viewBox="0 0 68 56" aria-hidden="true">
        <path d="M4 20 Q4 6 34 6 Q64 6 64 20 L64 25 L50 25 L48 17 Q34 13 20 17 L18 25 L4 25 Z" fill="#fff"/>
        <path d="M16 28 L52 28 L60 52 L8 52 Z" fill="#fff"/>
        <circle cx="34" cy="39" r="9" fill="#1b74c2"/>
        <circle cx="34" cy="39" r="4" fill="#fff"/>
      </svg>
      <div class="phone-numbers">01638405912<br>07481326970</div>
      <div class="email">enquiries@vorla-systems.net</div>
    </footer>
  </main>
</body>
</html>
```